Stationary Set Rebrand for Brennick

We are a Canadian Distribution and Service Company that was established in 1969. Over the past 5 decades we have expanded our business and have warehouses across Canada. We specialize in adhesive tapes, adhesives, films, safety, warehouse, shipping, janitorial and packaging supplies.

We have updated our logo design and would like a new corporate branding identity that includes a new fresh Stationary Set (Business Cards, Letterhead, Letterhead MS Word, Envelope, Presentation Folders, Email Signatures, Notepad Covers, etc.)

Target Market(s)

Industrial Business Sector

Font styles to use
Sans Serif

Colors
0054AA
0677BA
7BADD7
CADEEF
E8F1F8
0094D4
00A9DD
6FCCEA
C7EBF8
E9F6FB
00AB8E
00BBA5
67D7C9
C6EFE9
E9F9F6
EB3D1F
EC4F4E
F09395
F8D3D4
FCEDEE

Requirements
Should not have
• Colors not too light, darker colours preferred

```html
<!DOCTYPE html>
<html lang="en">
<head>
<meta charset="utf-8">
<title>Brennick Business Card</title>
<link href="https://fonts.googleapis.com/css2?family=Poppins:wght@400;500;600;700;800&family=Oswald:wght@600&display=swap" rel="stylesheet">
<style>
  :root {
    --page-bg: #efefef;
    --card-bg: #ffffff;
    --ink: #0b0b0b;
    --brand-red: #d71920;
    --gap-white: #ffffff;
  }
  * { margin: 0; padding: 0; box-sizing: border-box; }
  html, body {
    width: 1200px; height: 987px; overflow: hidden;
    background: var(--page-bg);
    font-family: "Poppins", sans-serif;
    color: var(--ink);
  }
  .stage { position: relative; width: 1200px; height: 987px; }
  .card {
    position: absolute; left: 245px; width: 710px; height: 405px;
    background: var(--card-bg); border-radius: 34px; overflow: hidden;
    box-shadow: 0 14px 30px rgba(0,0,0,0.28);
  }
  .card--front { top: 68px; }
  .card--back { top: 514px; }
  .card__band { position: absolute; left: 0; bottom: 0; width: 710px; height: 26px; display: block; }
  .wordmark {
    position: absolute; display: flex; align-items: center; gap: 12px;
    font-family: "Poppins", sans-serif; font-weight: 800; color: var(--ink);
    line-height: 1; letter-spacing: -1px;
  }
  .wordmark__dot { background: var(--brand-red); border-radius: 50%; flex: none; }
  .card--front .wordmark { left: 0; right: 0; top: 150px; justify-content: center; font-size: 84px; }
  .card--front .wordmark__dot { width: 22px; height: 22px; }
  .card--back .wordmark { left: 30px; top: 175px; font-size: 50px; }
  .card--back .wordmark__dot { width: 14px; height: 14px; }
  .divider {
    position: absolute; left: 356px; top: 98px; width: 1px; height: 206px;
    background: var(--brand-red);
  }
  .person { position: absolute; left: 403px; top: 98px; }
  .person__name { font-size: 35px; font-weight: 400; line-height: 1; letter-spacing: 0.5px; }
  .person__first { color: var(--brand-red); font-weight: 600; }
  .person__title { font-size: 19px; font-weight: 500; margin-top: 6px; letter-spacing: 0.3px; }
  .contacts { position: absolute; left: 403px; top: 189px; list-style: none; }
  .contacts li { display: flex; align-items: center; height: 26.5px; font-size: 21px; letter-spacing: 0.4px; }
  .contacts svg { width: 16px; height: 16px; margin-right: 13px; flex: none; }
  .address {
    position: absolute; left: 0; right: 0; top: 344px; text-align: center;
    font-size: 19px; letter-spacing: 0.3px;
  }
  .version-label {
    position: absolute; left: 977px; top: 448px;
    font-family: "Oswald", sans-serif; font-weight: 600; font-size: 66px;
    line-height: 1; letter-spacing: -1px; color: var(--ink);
  }
</style>
</head>
<body>
<div class="stage">

  <section class="card card--front">
    <div class="wordmark"><span>Brennick</span><span class="wordmark__dot"></span></div>
    <svg class="card__band" viewBox="0 0 710 26" aria-hidden="true">
      <polygon points="0,0 316,0 354,26 0,26" fill="var(--ink)"/>
      <polygon points="342,0 710,0 710,26 380,26" fill="var(--brand-red)"/>
    </svg>
  </section>

  <div class="version-label">Version-1</div>

  <section class="card card--back">
    <div class="wordmark"><span>Brennick</span><span class="wordmark__dot"></span></div>
    <div class="divider"></div>
    <div class="person">
      <div class="person__name"><span class="person__first">Maren</span> Tolliver</div>
      <div class="person__title">Founder &amp; CEO</div>
    </div>
    <ul class="contacts">
      <li>
        <svg viewBox="0 0 16 16" aria-hidden="true"><rect x="4" y="1" width="8" height="14" rx="1.5" fill="none" stroke="var(--brand-red)" stroke-width="1.4"/><line x1="7" y1="12.5" x2="9" y2="12.5" stroke="var(--brand-red)" stroke-width="1.2"/></svg>
        (555) 214-6630
      </li>
      <li>
        <svg viewBox="0 0 16 16" aria-hidden="true"><path d="M3 1.5l2.5 0 1.2 3.2-1.6 1.2c.8 1.8 2.2 3.2 4 4l1.2-1.6 3.2 1.2v2.5c0 .8-.7 1.5-1.5 1.5C7 13.5 2.5 9 1.5 3 1.5 2.2 2.2 1.5 3 1.5z" fill="var(--brand-red)"/><path d="M9.5 2.5a4 4 0 0 1 4 4M9.5 0.5a6 6 0 0 1 6 6" fill="none" stroke="var(--brand-red)" stroke-width="1"/></svg>
        (555) 214-6631
      </li>
      <li>
        <svg viewBox="0 0 16 16" aria-hidden="true"><circle cx="8" cy="8" r="7" fill="var(--brand-red)"/><path d="M4 5c2 0 2 2 3.5 2.5S7 11 8.5 12M10 3c0 2 2 2 3 3" fill="none" stroke="#fff" stroke-width="1.2"/></svg>
        info@brennickco.com
      </li>
      <li>
        <svg viewBox="0 0 16 16" aria-hidden="true"><rect x="1" y="4" width="14" height="11" fill="var(--brand-red)"/><path d="M1 4l7 6 7-6" fill="none" stroke="#fff" stroke-width="1.2"/><circle cx="8" cy="4" r="2.6" fill="#fff" stroke="var(--brand-red)" stroke-width="1"/></svg>
        www.brennickco.com
      </li>
    </ul>
    <div class="address">418 Harbourline Rd. Suite 120 Oakridge, ON L4K 2R9</div>
    <svg class="card__band" viewBox="0 0 710 26" aria-hidden="true">
      <polygon points="0,0 316,0 354,26 0,26" fill="var(--ink)"/>
      <polygon points="342,0 710,0 710,26 380,26" fill="var(--brand-red)"/>
    </svg>
  </section>

</div>
</body>
</html>
```